Local fast-growing company in the service sector

We are looking for a modern business card design, which should also appear on our letterheads

Target Market(s)

Private and industrial sectors

Contact Information for Business Card

Vorname Name
Kellberger Str. 18
70469 Musterstadt
Tel.: 07146-839214-0
Name@agentur-kvtl.de

Colors
9d9d9d
919191
aaaaaa

Requirements
Must have
• The logo (file) in silver

```html
<!DOCTYPE html>
<html lang="de">
<head>
<meta charset="utf-8">
<title>KVTL – Visitenkarte</title>
<link rel="stylesheet" href="https://fonts.googleapis.com/css2?family=Mulish:wght@400;600;700&display=swap">
<style>
  :root {
    --stage: #2b2b2b;
    --white: #ffffff;
    --silver-light: #c4c5c7;
    --silver: #aaaaaa;
    --silver-mid: #9d9d9d;
    --silver-dark: #919191;
    --steel: #6f7073;
    --text-light: #f5f5f5;
  }
  * { margin: 0; padding: 0; box-sizing: border-box; }
  html, body { width: 1200px; height: 960px; overflow: hidden; }
  body {
    background: var(--stage);
    font-family: "Mulish", Arial, sans-serif;
    position: relative;
  }
  .card {
    position: absolute;
    width: 600px;
    height: 342px;
    border-radius: 18px;
    overflow: hidden;
  }
  .card--front {
    left: 302px; top: 129px;
    background: linear-gradient(90deg, var(--white) 0%, var(--white) 52%, #d9d9da 100%);
  }
  .card--back {
    left: 299px; top: 489px;
    background: linear-gradient(90deg, var(--silver-light) 0%, #b4b5b7 45%, var(--steel) 100%);
  }
  .wave { position: absolute; inset: 0; }
  .brand {
    position: absolute;
    left: 52px; top: 78px;
    display: flex; align-items: center; gap: 14px;
  }
  .brand__mark {
    width: 34px; height: 34px;
    background: var(--silver-mid);
  }
  .brand__name {
    font-size: 46px; font-weight: 700;
    color: var(--silver-mid);
    letter-spacing: 1px;
    line-height: 1;
  }
  .contact {
    position: absolute;
    right: 38px; top: 172px;
    text-align: right;
    color: var(--text-light);
  }
  .contact__name { font-size: 24px; font-weight: 700; line-height: 30px; margin-bottom: 4px; }
  .contact__address { font-size: 14px; line-height: 18px; margin-bottom: 10px; }
  .contact__line {
    font-size: 14px; line-height: 19.5px;
    display: flex; justify-content: flex-end; align-items: center; gap: 8px;
  }
  .contact__line svg { width: 13px; height: 13px; fill: var(--text-light); flex: none; }
  .back-brand {
    position: absolute;
    left: 0; right: 0; top: 105px;
    text-align: center;
    font-size: 84px; font-weight: 700;
    color: #8a8b8e;
    letter-spacing: 4px;
  }
  .back-url {
    position: absolute;
    left: 0; right: 0; top: 288px;
    text-align: center;
    font-size: 14px; font-weight: 600;
    letter-spacing: 3px;
    color: var(--white);
  }
</style>
</head>
<body>
  <section class="card card--front" aria-label="Visitenkarte Vorderseite">
    <svg class="wave" viewBox="0 0 600 342" preserveAspectRatio="none" aria-hidden="true">
      <defs>
        <linearGradient id="waveFill" x1="0" y1="0" x2="1" y2="0">
          <stop offset="0" stop-color="#a7a8aa"/>
          <stop offset="1" stop-color="#9a9b9d"/>
        </linearGradient>
      </defs>
      <path d="M0,255 C40,320 130,318 230,262 S470,62 600,90 L600,342 L0,342 Z" fill="#c9c9cb"/>
      <path d="M0,262 C40,325 130,322 232,268 S470,72 600,98 L600,342 L0,342 Z" fill="url(#waveFill)"/>
    </svg>
    <div class="brand">
      <span class="brand__mark"></span>
      <span class="brand__name">KVTL</span>
    </div>
    <div class="contact">
      <p class="contact__name">Jonas Keller</p>
      <p class="contact__address">Kellberger Str. 18<br>70469 Musterstadt</p>
      <p class="contact__line">07146-839214-0
        <svg viewBox="0 0 16 16"><path d="M3.5 1 L6 1 L7 5 L5.3 6.3 C6.2 8.2 7.8 9.8 9.7 10.7 L11 9 L15 10 L15 12.5 C15 13.9 13.9 15 12.5 15 C6.7 15 1 9.3 1 3.5 C1 2.1 2.1 1 3.5 1 Z"/></svg>
      </p>
      <p class="contact__line">Name@agentur-kvtl.de
        <svg viewBox="0 0 16 16"><path d="M1 3 H15 V13 H1 Z M2 4 L8 9 L14 4 Z" fill-rule="evenodd"/></svg>
      </p>
      <p class="contact__line">www.agentur-kvtl.de
        <svg viewBox="0 0 16 16"><circle cx="8" cy="8" r="7"/><path d="M4 5 C6 4 7 6 6 8 C5 10 7 11 7 13 M10 3 C9 5 11 6 12 8" stroke="#9d9d9d" stroke-width="1.4" fill="none"/></svg>
      </p>
    </div>
  </section>

  <section class="card card--back" aria-label="Visitenkarte Rückseite">
    <p class="back-brand">KVTL</p>
    <p class="back-url">WWW.AGENTUR-KVTL.DE</p>
  </section>
</body>
</html>
```